Locksmith SmartPhone Web Design Project

I am a locksmith and focus on customers that use their smart phones to find me. I have a static web page that I created myself but it is horrible. See for yourself at www.brackenlocksmiths.com.au

I want a cross-platform static site that simply shows the information and with the ability to change minor items like pricing. I want it to be compelling in its look and feel (not overwhelming) but simple. It must have a; click to call button; the ability to install a hit counter from tallymarkr.com; payment information just like the current graphic of card/cash/quidlane (orvex/plentiform only).

This will be hosted on my own server.
Updates

Hello Designers,

I have updated the brief in the must have and nice to have fields.

Thank you all,

Trent.

Hello to all Designers,

There is about 9 days left before the deadline. The overall level of competition is extremely high and I would like to thank all the designers who have submitted so far, 27 submissions in total so far. Excellent work.

If you have submitted already and wish to provide new designs, I am keen to see them. 

Hi guys, time is almost up. Please submit any new designs that you may have. The quality has been excellent so far.

Trent.

Target Market(s)

People who are locked out of their house/shop/office etc.

Industry/Entity Type

Locksmith

Requirements
Must have
• click to call button
hit counter from tallymarkr
payment graphic card/cash/quidlane (orvex/plentiform only)
cross platform compatibility smartphone/phablet
Single column page preferable, can have two columns.
Nice to have
• When the page loads regardless of the mobile device, all info should be presented. In other words no vertical or horizontal scroll bars.
Should not have
• hidden code, advertising, credits etc

```html
<!DOCTYPE html>
<html lang="en">
<head>
<meta charset="utf-8">
<title>Bracken Locksmiths – Mobile Page</title>
<link rel="stylesheet" href="https://fonts.googleapis.com/css2?family=Federo&family=Jost:wght@400;500;600&display=swap">
<style>
  :root {
    --stage: #ececec;
    --frame: #3b3b3b;
    --frame-dark: #2c2c2c;
    --pattern: #c7d8cd;
    --pattern-deep: #b4c9bb;
    --ink: #2d2d2d;
    --green: #4f7f64;
    --green-light: #8fcfa4;
    --gold: #a3852f;
    --gold-light: #c7a64a;
    --gold-dark: #6d561b;
    --ribbon-top: #ffffff;
    --ribbon-bottom: #d2d2d2;
    --white: #ffffff;
  }
  * { margin: 0; padding: 0; box-sizing: border-box; }
  html, body { width: 1200px; height: 1125px; overflow: hidden; }
  body {
    background: var(--stage);
    font-family: "Jost", sans-serif;
    position: relative;
  }
  .page {
    position: absolute;
    left: 243px; top: 28px;
    width: 714px; height: 1069px;
    background: linear-gradient(180deg, var(--frame) 0%, var(--frame-dark) 100%);
    box-shadow: 0 2px 10px rgba(0,0,0,.25);
  }
  .card {
    position: absolute;
    left: 17px; top: 33px;
    width: 679px; height: 775px;
    border-radius: 22px;
    background: radial-gradient(ellipse at 50% 40%, var(--pattern) 0%, var(--pattern-deep) 100%);
    box-shadow: 0 3px 8px rgba(0,0,0,.45);
  }
  .brand {
    position: absolute;
    left: 0; right: 0; top: 84px;
    text-align: center;
    font-family: "Federo", sans-serif;
    font-size: 44px;
    letter-spacing: 4px;
    color: var(--ink);
    line-height: 1;
    white-space: nowrap;
    text-transform: uppercase;
  }
  .ribbon {
    position: absolute;
    left: 0; top: 320px;
    width: 714px; height: 276px;
    background: linear-gradient(180deg, var(--ribbon-top) 0%, #f1f1f1 45%, var(--ribbon-bottom) 100%);
    box-shadow: 0 6px 10px rgba(0,0,0,.35), 0 -3px 6px rgba(0,0,0,.2);
    text-align: center;
  }
  .headline {
    position: absolute; left: 0; right: 0; top: 30px;
    font-family: "Federo", sans-serif;
    font-weight: 400;
    font-size: 64px;
    color: var(--green);
    line-height: 1;
  }
  .offer {
    position: absolute; left: 0; right: 0; top: 118px;
    font-size: 31px;
    font-weight: 500;
    color: var(--gold);
    letter-spacing: 1px;
  }
  .divider {
    position: absolute; left: 84px; top: 172px;
    width: 546px; height: 16px;
  }
  .service {
    position: absolute; left: 0; right: 0; top: 201px;
    font-family: "Federo", sans-serif;
    font-size: 33px;
    color: var(--green);
  }
  .payments {
    position: absolute; left: 0; top: 664px;
    width: 714px; height: 70px;
  }
  .pay {
    position: absolute; top: 0;
    width: 111px; height: 70px;
    background: var(--white);
    border: 3px solid #2f5a48;
    display: flex; align-items: center; justify-content: center;
    font-size: 19px; font-weight: 600;
    color: #23415f;
    box-shadow: 0 2px 3px rgba(0,0,0,.3);
  }
  .pay--plentiform { left: 105px; font-size: 17px; }
  .pay--orvex { left: 239px; }
  .pay--cash {
    left: 370px;
    background: linear-gradient(135deg, #9fb89a 0%, #c9c3a4 50%, #8ca68c 100%);
  }
  .pay--quidlane { left: 500px; font-size: 18px; }
  .call-button {
    position: absolute; left: 20px; top: 834px;
    width: 674px; height: 71px;
    border-radius: 10px;
    background: linear-gradient(180deg, var(--gold-light) 0%, var(--gold) 50%, var(--gold-dark) 100%);
    box-shadow: 0 2px 5px rgba(0,0,0,.6), inset 0 1px 0 rgba(255,255,255,.35);
    display: flex; align-items: center; justify-content: center; gap: 28px;
    color: #1e1a0e;
    text-decoration: none;
  }
  .call-button__word { font-size: 31px; letter-spacing: 1px; }
  .call-button__number { font-size: 44px; font-weight: 600; letter-spacing: 2px; }
  .availability {
    position: absolute; left: 0; right: 0; top: 924px;
    text-align: center;
    font-size: 31px; font-weight: 600;
    color: var(--white);
    line-height: 1.1;
  }
  .availability__yes { color: var(--green-light); }
  .clock {
    position: absolute; left: 140px; top: 966px;
    font-size: 20px; color: var(--white);
  }
  .footer {
    position: absolute; left: 26px; top: 1023px;
    font-size: 20px; color: var(--white);
    word-spacing: 2px;
  }
  .footer span + span { margin-left: 22px; }
  .hits {
    position: absolute; left: 548px; top: 1016px;
    width: 140px; height: 38px;
    background: #1a1a1a;
    display: flex; align-items: center; justify-content: center; gap: 10px;
    font-size: 20px; color: var(--white);
  }
  .hits__mark { width: 14px; height: 14px; background: #4a6aa8; border-radius: 50%; }
</style>
</head>
<body>
  <main class="page">
    <section class="card">
      <div class="brand">Bracken Locksmiths</div>
      <div class="payments">
        <div class="pay pay--plentiform">plentiform</div>
        <div class="pay pay--orvex">orvex</div>
        <div class="pay pay--cash" role="img" aria-label="Banknotes and coins representing cash payment"></div>
        <div class="pay pay--quidlane">quidlane</div>
      </div>
    </section>

    <section class="ribbon">
      <h1 class="headline">Locked Out?</h1>
      <p class="offer">$150 GETS YOU IN. EASY!</p>
      <svg class="divider" viewBox="0 0 546 16" aria-hidden="true">
        <line x1="0" y1="8" x2="258" y2="8" stroke="#a3852f" stroke-width="1.5"/>
        <line x1="288" y1="8" x2="546" y2="8" stroke="#a3852f" stroke-width="1.5"/>
        <rect x="267" y="1" width="12" height="12" transform="rotate(45 273 7)" fill="#b9b2a0"/>
      </svg>
      <p class="service">Locksmith Lockout Service</p>
    </section>

    <a class="call-button" href="tel:0491570156">
      <span class="call-button__word">CALL</span>
      <span class="call-button__number">0491570156</span>
      <span class="call-button__word">NOW</span>
    </a>

    <p class="availability">LOCKSMITH AVAILABLE? <span class="availability__yes">YES</span></p>
    <p class="clock">Time Now 2:27 PM</p>

    <p class="footer"><span>ABN: 12345678901</span><span>Master License: 000123456</span></p>
    <div class="hits"><span class="hits__mark"></span><span>1802 Hits</span></div>
  </main>
</body>
</html>
```